Build a landing page to promote a service (dialler consultation and support).

We are a call centre consultation firm and we need a landing page to promote a service. The service is Tormalux dialler consultation and support.
If you do not know what Tormalux is, please do some quick "Zorvex" research for more information.
The landing page will be promoted with a paid advertisement, so we want something that is simple, and explains exactly what service we offer.
There are two objectives for the landing page:
1) A "call to action" which directs the user to a contact page, including a form plus all of our contact details.
2) A form for them viewers to enter their details to get a "FREE" quote for their project. This form should be placed on the main page.
Notes:
The call to action will require the viewer to enter their name, email, phone number as well as a description of their request. There will also need to be a drop down menu for the type of quote. This menu should have the following options:
1) Tormalux support
2) Tormalux hosting
3) Tormalux customisation
4) Other
We need 2 pages in total:
1) Main landing page
This is the home page. It will need to clearly indicate our services and our key selling features.
Services:
* Tormalux support
* Tormalux hosting
* Tormalux customisation
Key Selling Features:
* Australian based
* PCI complaint
* 10+ years of dialler and call centre experience
* we run a sister company which is a highly reputable 40 seat call centre, so we know first hand about call centre technology.
The main landing page will have an "about us" section with a few paragraphs about how we got started.
-------------------------------------------------------------------------
2) Contact page
All of our contact details will live on this page, as well as a contact form.
Other notes:
We will be self hosting the landing page.
We already have a domain name.
The design must be clean and incorporate our logo, as well as it's colours. (Logo attached)
We want a fully function HTML landing page, not just a "PSD" design.
The page must be mobile optimised.
Anyone using Tormalux software.

```html
<!DOCTYPE html>
<html lang="en">
<head>
<meta charset="utf-8">
<title>Callvane – Tormalux Dialler Consultation &amp; Support</title>
<link href="https://fonts.googleapis.com/css2?family=Jost:wght@400;500;600&display=swap" rel="stylesheet">
<style>
  :root{
    --blue:#1a8fd0;
    --teal:#23b59d;
    --ink:#333b40;
    --line:#cfd4d8;
    --white:#ffffff;
    --net-a:#3a5a99;
    --net-b:#5ab4e8;
    --net-c:#1a7db8;
    --net-d:#d8322b;
  }
  *{box-sizing:border-box;margin:0;padding:0}
  html,body{width:1200px;height:1023px;overflow:hidden;background:var(--white)}
  body{position:relative;font-family:"Jost",sans-serif;color:var(--ink)}

  .site-header{position:absolute;left:0;top:0;width:1200px;height:64px;background:var(--white);z-index:3}
  .contact-strip{position:absolute;left:140px;top:21px;display:flex;align-items:center;font-size:12px}
  .contact-strip .phone{font-size:15px;display:flex;align-items:center;gap:8px}
  .contact-strip .sep{width:1px;height:18px;background:var(--line);margin:0 14px}
  .contact-strip .mail{display:flex;align-items:center;gap:8px}

  .brand-badge{position:absolute;left:500px;top:-70px;width:200px;height:200px;border-radius:50%;background:var(--white);z-index:4;display:flex;flex-direction:column;align-items:center;justify-content:flex-end;padding-bottom:36px}
  .brand-badge .dot{width:56px;height:56px;border-radius:50%;background:var(--blue);border:3px solid var(--white);box-shadow:0 0 0 2px var(--teal);margin-bottom:6px}
  .brand-badge .name{font-size:25px;font-weight:500;color:var(--blue);letter-spacing:1px;line-height:1}

  .quote-btn{position:absolute;left:771px;top:15px;width:150px;height:31px;border-radius:16px;background:var(--teal);color:var(--white);font-weight:600;font-size:14px;letter-spacing:.6px;padding-left:22px;line-height:31px}
  .quote-btn .knob{position:absolute;right:-2px;top:-2px;width:35px;height:35px;border-radius:50%;background:var(--blue);border:3px solid var(--white);box-shadow:0 0 0 1px var(--teal)}

  .social{position:absolute;display:flex;gap:3px}
  .social span{width:26px;height:26px;border-radius:50%;display:flex;align-items:center;justify-content:center;font-size:10px;font-weight:600;color:var(--white);letter-spacing:0}
  .social.top{left:946px;top:18px}
  .social.top span:nth-child(1){background:var(--net-a)}
  .social.top span:nth-child(2){background:var(--net-b)}
  .social.top span:nth-child(3){background:var(--net-c)}
  .social.top span:nth-child(4){background:var(--net-d)}

  .hero{position:absolute;left:0;top:64px;width:1200px;height:480px}

  .quote-form{position:absolute;left:140px;top:605px;width:438px}
  .section-title{font-size:26px;font-weight:600;color:var(--blue);letter-spacing:.5px;line-height:36px}
  .section-title em{font-style:normal;color:var(--teal)}
  .field{position:absolute;border:1px solid var(--line);border-radius:3px;background:var(--white);font-size:14px;padding:0 16px;line-height:36px;color:var(--ink)}
  .f-name{left:2px;top:58px;width:211px;height:38px}
  .f-email{left:226px;top:58px;width:211px;height:38px}
  .f-phone{left:2px;top:108px;width:211px;height:38px}
  .f-type{left:226px;top:108px;width:211px;height:38px;display:flex;justify-content:space-between;align-items:center}
  .f-msg{left:2px;top:157px;width:435px;height:101px;line-height:1;padding-top:13px}
  .submit-btn{position:absolute;left:2px;top:283px;width:146px;height:30px;border-radius:15px;background:var(--teal);color:var(--white);font-weight:600;font-size:13px;letter-spacing:.6px;line-height:30px;padding-left:22px}
  .submit-btn .knob{position:absolute;right:-2px;top:-2px;width:34px;height:34px;border-radius:50%;background:var(--blue);border:3px solid var(--white);box-shadow:0 0 0 1px var(--teal)}

  .divider{position:absolute;left:602px;top:615px;width:1px;height:342px;background:#e6e8ea}

  .company{position:absolute;left:634px;top:605px;width:424px}
  .map{position:absolute;left:0;top:58px;width:424px;height:148px;border:1px solid var(--line);border-radius:2px;background:linear-gradient(90deg,#e9ebee 0%,#e9ebee 22%,#c8e6c0 30%,#c8e6c0 42%,#ece9e4 52%,#eeeeee 80%,#f4e4a8 100%)}
  .info-row{position:absolute;display:flex;align-items:center;gap:14px;font-size:14px;white-space:nowrap}
  .info-row .ico{width:36px;height:36px;border-radius:50%;background:var(--blue);border:2px solid var(--white);box-shadow:0 0 0 1px var(--blue);display:flex;align-items:center;justify-content:center}
  .r-addr{left:0;top:235px}
  .r-phone{left:0;top:286px;font-size:16px}
  .r-mail{left:190px;top:286px}

  .site-footer{position:absolute;left:0;top:988px;width:1200px;height:35px;background:var(--blue);color:var(--white);font-size:12px}
  .site-footer .copy{position:absolute;left:142px;top:9px}
  .social.bottom{right:141px;top:4px;gap:7px}
  .social.bottom span{width:27px;height:27px;background:var(--white);color:var(--blue)}
</style>
</head>
<body>

<header class="site-header">
  <div class="contact-strip">
    <div class="phone">
      <svg width="20" height="20" viewBox="0 0 24 24" fill="none" stroke="#1a8fd0" stroke-width="1.6"><path d="M5 3l3 0 2 5-2 1.5a11 11 0 0 0 6 6L15.5 13l5 2v3a2 2 0 0 1-2 2A16 16 0 0 1 3 5a2 2 0 0 1 2-2z"/></svg>
      555-014-2290
    </div>
    <span class="sep"></span>
    <div class="mail">
      <svg width="20" height="20" viewBox="0 0 24 24" fill="none" stroke="#1a8fd0" stroke-width="1.6"><rect x="3" y="6" width="18" height="14" rx="1"/><path d="M3 7l9 7 9-7"/></svg>
      hello@callvane.net
    </div>
  </div>
  <a class="quote-btn">Get A Quote<span class="knob"></span></a>
  <div class="social top" aria-label="Social links"><span>Qo</span><span>Vy</span><span>Ru</span><span>Ze</span></div>
</header>

<div class="brand-badge"><span class="dot"></span><span class="name">Callvane</span></div>

<svg class="hero" width="1200" height="480" viewBox="0 0 1200 480">
  <defs>
    <linearGradient id="heroFill" x1="0" y1="0" x2="0" y2="1">
      <stop offset="0" stop-color="#aeaca9"/>
      <stop offset=".45" stop-color="#cbc6bf"/>
      <stop offset=".75" stop-color="#dcc9ab"/>
      <stop offset="1" stop-color="#c4a47c"/>
    </linearGradient>
    <clipPath id="heroClip"><path d="M0 0H1200V396Q600 552 0 396Z"/></clipPath>
  </defs>
  <rect width="1200" height="480" fill="url(#heroFill)" clip-path="url(#heroClip)" role="img" aria-label="Photo of four wooden blocks printed with phone, envelope, at-sign and mobile icons on a desk"/>
  <path d="M0 396Q600 552 1200 396" fill="none" stroke="#23b59d" stroke-width="3"/>
</svg>

<section class="quote-form">
  <h2 class="section-title">Request A <em>Free Quote</em></h2>
  <div class="field f-name">Name</div>
  <div class="field f-email">Email</div>
  <div class="field f-phone">Phone</div>
  <div class="field f-type">Quote for
    <svg width="10" height="6" viewBox="0 0 10 6"><path d="M1 1l4 4 4-4" fill="none" stroke="#333b40" stroke-width="1.3"/></svg>
  </div>
  <div class="field f-msg">Message</div>
  <a class="submit-btn">Submit Now<span class="knob"></span></a>
</section>

<div class="divider"></div>

<section class="company">
  <h2 class="section-title">Callvane</h2>
  <div class="map" role="img" aria-label="Street map showing the office location"></div>
  <div class="info-row r-addr">
    <span class="ico"><svg width="14" height="18" viewBox="0 0 14 18"><path d="M7 1a6 6 0 0 1 6 6c0 4-6 10-6 10S1 11 1 7a6 6 0 0 1 6-6z" fill="none" stroke="#fff" stroke-width="1.6"/><circle cx="7" cy="7" r="2" fill="#fff"/></svg></span>
    14/9 Harbour Lane Westdale, QLD 4100
  </div>
  <div class="info-row r-phone">
    <span class="ico"><svg width="16" height="16" viewBox="0 0 24 24"><path d="M5 3h3l2 5-2 1.5a11 11 0 0 0 6 6L15.5 13l5 2v3a2 2 0 0 1-2 2A16 16 0 0 1 3 5a2 2 0 0 1 2-2z" fill="#fff"/></svg></span>
    555-014-2290
  </div>
  <div class="info-row r-mail">
    <span class="ico"><svg width="18" height="14" viewBox="0 0 18 14"><rect x="1" y="1" width="16" height="12" rx="1" fill="none" stroke="#fff" stroke-width="1.5"/><path d="M1 2l8 6 8-6" fill="none" stroke="#fff" stroke-width="1.5"/></svg></span>
    hello@callvane.net
  </div>
</section>

<footer class="site-footer">
  <p class="copy">Copyright © 2018 Callvane. All Rights Reserved</p>
  <div class="social bottom" aria-label="Social links"><span>Qo</span><span>Vy</span><span>Ru</span><span>Ze</span></div>
</footer>

</body>
</html>
```